Tallow Reed Software

We are a software company selling endpoint visibility, access and security technology to enterprise-level IT departments.

Our technology helps organizations gain comprehensive visibility into and control over devices accessing their corporate network so they can quickly identify and address suspicious activity on the network that could lead to potential threats like data breaches.

This technology can cost organizations upwards of $1M - depending on the size of the organization. Our primary clients are Pinnacle 2,000 companies.

We want a professional, polished business card to represent our new brand.

Info fields to include on the card:
Name
Job Title
Office Phone #
Cell Phone #
Email address
Address: 4270 Vestridge Pond Blvd., Ste. 2600, Bloomington, MN 55812
Website address: www.tallowreedsoftware.example
Tagline: Discover the edge. Optimize the whole.

Logo files and color specs document are attached. Would like color scheme to coordinate with the logo.

Also looking at stationary/envelope designs in conjunction with the business card designs. Received very few designs that included the stationary.

Software

```html
<!DOCTYPE html>
<html lang="en">
<head>
<meta charset="utf-8">
<title>Tallow Reed Software — Business Card</title>
<link rel="stylesheet" href="https://fonts.googleapis.com/css2?family=Montserrat:wght@500;600&family=Open+Sans:wght@400;600;700&display=swap">
<style>
  :root {
    --backdrop: #ece9e6;
    --card: #ffffff;
    --copper: #8e4f3f;
    --copper-light: #b87a62;
    --ink: #3a3a3a;
    --ink-soft: #6b6b6b;
    --dot-grey: #d9d9d9;
    --dot-dark: #a8a8a8;
  }
  * { margin: 0; padding: 0; box-sizing: border-box; }
  html, body { width: 1200px; height: 913px; overflow: hidden; }
  body {
    background: var(--backdrop);
    position: relative;
    font-family: "Open Sans", Arial, sans-serif;
  }
  .card {
    position: absolute;
    width: 530px;
    height: 303px;
    background: var(--card);
    box-shadow: 0 2px 6px rgba(0,0,0,0.12);
    overflow: hidden;
  }
  .card--front { left: 50px; top: 150px; }
  .card--back { left: 620px; top: 440px; }

  .front-decor {
    position: absolute;
    left: 330px; top: -90px;
    width: 300px; height: 260px;
    background: radial-gradient(ellipse closest-side at 50% 50%, var(--dot-dark) 0%, var(--dot-grey) 45%, rgba(255,255,255,0) 100%);
  }
  .brand {
    position: absolute;
    left: 0; right: 0;
    top: 116px;
    display: flex;
    align-items: center;
    justify-content: center;
    gap: 14px;
  }
  .brand-mark {
    width: 14px; height: 14px;
    background: var(--copper);
  }
  .brand-name {
    font-family: "Montserrat", Arial, sans-serif;
    font-weight: 600;
    color: var(--copper);
    font-size: 26px;
    letter-spacing: 4px;
    line-height: 1.2;
    text-transform: uppercase;
  }
  .brand-name small {
    display: block;
    font-size: 14px;
    letter-spacing: 9px;
  }
  .tagline {
    position: absolute;
    left: 0; right: 0;
    bottom: 34px;
    text-align: center;
    font-family: "Montserrat", Arial, sans-serif;
    font-weight: 500;
    font-size: 11px;
    letter-spacing: 1.5px;
    color: var(--ink-soft);
  }

  .back-decor {
    position: absolute;
    left: 30px; top: 60px;
    width: 220px; height: 190px;
    background: radial-gradient(ellipse closest-side at 50% 50%, var(--copper-light) 0%, #d7b4a6 40%, #ececec 70%, rgba(255,255,255,0) 100%);
  }
  .contact {
    position: absolute;
    left: 270px; top: 62px;
    color: var(--ink-soft);
    font-size: 11px;
    line-height: 1.5;
  }
  .contact-name { color: var(--ink); font-weight: 700; font-size: 15px; line-height: 1.2; }
  .contact-title { margin-bottom: 14px; }
  .contact-address { margin-bottom: 8px; }
  .contact-row { display: flex; align-items: center; gap: 7px; }
  .contact-row svg { width: 10px; height: 10px; fill: var(--copper); flex: none; }
  .contact-web { color: var(--copper); }
</style>
</head>
<body>

<section class="card card--front" aria-label="Business card front">
  <div class="front-decor" role="img" aria-label="Decorative field of soft grey dots"></div>
  <div class="brand">
    <span class="brand-mark"></span>
    <p class="brand-name">Tallow Reed<small>Software</small></p>
  </div>
  <p class="tagline">Discover the edge. Optimize the whole.</p>
</section>

<section class="card card--back" aria-label="Business card back">
  <div class="back-decor" role="img" aria-label="Decorative grid of copper and grey dots"></div>
  <div class="contact">
    <p class="contact-name">Your Long Name</p>
    <p class="contact-title">Managing Director</p>
    <p class="contact-address">4270 Vestridge Pond Blvd.<br>Ste. 2600, Bloomington, MN 55812</p>
    <p class="contact-row"><svg viewBox="0 0 10 10"><rect x="2" y="0" width="6" height="10" rx="1"/></svg>00.123.123.123</p>
    <p class="contact-row"><svg viewBox="0 0 10 10"><path d="M1 4 Q5 0 9 4 L8 5 L6 4 L6 3 Q5 2.5 4 3 L4 4 L2 5 Z M2 6 H8 V9 H2 Z"/></svg>00.00.00.0000</p>
    <p class="contact-row"><svg viewBox="0 0 10 10"><path d="M0 2 H10 V8 H0 Z M0 2 L5 6 L10 2" stroke="#fff" stroke-width="0.8"/></svg>yourname@tallowreedsoftware.example</p>
    <p class="contact-row contact-web"><svg viewBox="0 0 10 10"><circle cx="5" cy="5" r="5"/></svg>www.tallowreedsoftware.example</p>
  </div>
</section>

</body>
</html>
```